Wordpress Theme for Medical Clinics

** Please view updated Sitemap2.pdf doc to clarify some confusion ***

This is a multiuser WordPress subscription site for medical clinics. Please see attachment for sitemap. Please do not include extra content like social media icons, search bars, or images. If you have questions, please ask for clarification.
The site contains the following pages and sub-pages:

1. Home
2. Our Clinic
2a. Our Clinic > Mission
2b. Our Clinic > Services
2c. Our Clinic > Clinic Policies
2d. Our Clinic > Schedules
3. Our Staff
3a. Our Staff > [Staff member page]
4. Resources
4a. Resources > Patient Health (index)
4b. Resources > Patient Health (index) > [post]
4c. Resources > Links
4d. Resources > Forms
5. Alerts
5a. Alerts > [Alert Page]
6. Contact Us

Includes the Following Pages, Subpages, and Content
1. Home
a. About Us
b. Our Staff
c. Bulletins
d. Accepting New Patients (shown as an alert widget)
e. Links
i. Physician Toolbox
ii. Book an Appointment
f. Clinic Policies
i. Show first 3 policies (e.g. Late Arrivals, Missed Appointments, Fees)
ii. Link to Clinic Policies page
g. Primary widget (displayed on all pages)
i. Hours of operation
ii. Contact Info
1. Tel
2. Fax
3. Email
4. Address
5. Get directions (link to Wayline Maps)
2. Our Clinic
a. Main Page
i. Clinic Name
ii. Overview
iii. Languages Spoken
iv. Secondary Navigation
1. Mission
2. Services
3. Clinic Policies
4. Schedules (see attachment)
b. Our Clinic > Mission
c. Our Clinic > Services
i. For each service include service TITLE and DESCRIPTION
d. Our Clinic > Clinic Policies
i. For each policy include policy TITLE and DESCRIPTION
ii. Include the following policies in mockup
1. Late arrivals
2. Missed appointments
3. Fees for missed appointments
4. Referrals and follow-ups
5. Services not covered by RDA
6. Information for LTF patients
7. Medical Legal Reports
e. Our Clinic > Schedules
3. Our Staff
a. Main Page
i. Display a list of staff members. Include NAME and DESIGNATION
b. Our Staff > [Staff Name]
i. Include NAME, PICTURE, DESIGNATION, and BIO
4. Resources
a. Resources > Patient Health
i. Main Page
1. Posts (ordered by date)
a. Title
b. Summary
2. Side Navigation
a. Post Categories
ii. Patient Health > [post title]
1. Title
2. Post Category
3. Date
4. Author
5. Summary
6. Body
b. Resources > Links
1. Secondary Navigation - Categories
a. Sample Categories:
i. Local Services
ii. RDA and Drug Coverage
iii. Mental Health Resources
2. Category page
a. Include the following links in the 'Local Services' category
i. Hypertension clinics
ii. Home Care services
iii. Vaccine Clinics
c. Resources > Forms
i. Display a table with form TITLE and CATEGORY
ii. Side Navigation
1. Form Categories
a. Use the following sample Categories
i. Referrals
ii. Insurance
iii. Intake
iv. Discharge
v. Waivers
5. Alerts
a. Main page
i. List of all Alert posts
1. Include post TITLE as a link to the post
ii. Side Navigation
1. Alerts Archive
a. shown as Month + Number of posts
iii. Alerts > [Alert page]
1. Include TITLE, DATE, AUTHOR, BODY
6. Contact Us
a. Map
b. Hours of operation
c. Address
d. Phone number
e. Fax number
e. Fax number
f. Map
g. Email

Design notes:
- fixed width
- responsive (need designs for mobile, tablet, and desktop)
- simple, dark font, white background
- use Font Awesome icons where needed
- user adds own logo

Target Market(s)

Medical Clinics

Industry/Entity Type

Medical

Number of Pages Required

5+ page

Font styles to use
Serif
Sans Serif

Requirements
Must have
• Please keep designs very simple.
• Examples:
• https://www.quolbin.com/install
• http://www.ventrohax.com/company/about-us
• http://brindlequota.org/
• http://www.trosk.com/
Should not have
• Minimal or no use of shadows and gradients

```html
<!DOCTYPE html>
<html lang="en">
<head>
<meta charset="utf-8">
<title>Clinic Name – Home</title>
<link href="https://fonts.googleapis.com/css2?family=Open+Sans:wght@400;600;700&display=swap" rel="stylesheet">
<style>
:root{
  --blue:#2aa9e0;
  --blue-soft:#bfe5f5;
  --ink:#333333;
  --line:#e6e6e6;
  --page:#f3f3f3;
  --white:#ffffff;
  --footer:#262626;
}
*{box-sizing:border-box;margin:0;padding:0}
html,body{width:1200px;height:3258px;overflow:hidden}
body{font-family:"Open Sans",Arial,sans-serif;color:var(--ink);background:var(--white);position:relative}
a{color:var(--blue);text-decoration:none}

/* header */
.site-header{position:absolute;top:0;left:0;width:1200px;height:100px;background:var(--white)}
.brand{position:absolute;left:73px;top:34px;font-size:22px;font-weight:700;letter-spacing:.5px;color:var(--ink)}
.main-nav a{position:absolute;top:38px;font-size:13px;font-weight:600;color:var(--ink);text-transform:uppercase;letter-spacing:.3px}
.main-nav a.active{color:var(--blue)}
.main-nav a.active::after{content:"";position:absolute;left:2px;right:2px;bottom:-12px;height:3px;background:var(--blue)}

/* hero */
.hero{position:absolute;top:100px;left:0;width:1200px;height:660px;background:linear-gradient(100deg,#e9eef0 0%,#dfe7ea 45%,#cfe0ea 70%,#a9cbe0 100%)}
.hero-arrow{position:absolute;top:276px;width:40px;height:40px;border-radius:50%;background:#555;display:flex;align-items:center;justify-content:center}
.hero-title{position:absolute;left:171px;top:420px;color:#1e1e1e;font-size:31px;line-height:42px;text-transform:uppercase;font-weight:400}
.hero-title strong{display:block;font-weight:700}

/* info cards */
.info-band{position:absolute;top:760px;left:0;width:1200px;height:407px;background:var(--page)}
.card{position:absolute;top:711px;width:331px;height:389px;background:var(--white);padding:28px 32px}
.card h3{font-size:20px;font-weight:600;text-transform:uppercase;display:flex;align-items:center;gap:10px;color:#2a2a2a;margin-bottom:26px}
.card p{font-size:13px;color:#555}
.btn{display:inline-block;border:2px solid var(--blue);color:var(--blue);font-size:13px;font-weight:600;text-transform:uppercase;padding:9px 14px;background:var(--white)}
.card .btn{position:absolute;left:33px;bottom:27px}
.rows{list-style:none}
.rows li{display:flex;border-bottom:1px solid var(--line);font-size:12.5px;height:41px;align-items:center}
.rows li:last-child{border-bottom:0}
.rows b{width:125px;flex-shrink:0;font-weight:700;text-transform:uppercase;font-size:12px}
.rows span{color:var(--blue)}
.contact-rows li span{color:#555}
.contact-rows li.tall{height:80px;align-items:flex-start;padding-top:12px;line-height:17px}

/* about */
.about{position:absolute;top:1167px;left:0;width:1200px;height:326px;background:linear-gradient(180deg,#4cb8e6,#36a6dc);color:var(--white);text-align:center}
.about h2{margin-top:62px;font-size:27px;font-weight:700;text-transform:uppercase;display:flex;justify-content:center;align-items:center;gap:12px}
.about p{width:1040px;margin:28px auto 0;font-size:15px;line-height:27px}
.about p + p{margin-top:26px}

/* section titles */
.section-title{position:absolute;left:0;width:1200px;text-align:center;font-size:28px;font-weight:700;text-transform:uppercase;display:flex;justify-content:center;align-items:center;gap:12px;color:#222}

/* staff */
.staff-photo{position:absolute;left:95px;top:1621px;width:516px;height:442px;background:radial-gradient(ellipse at 50% 45%,#f1ece6 0%,#f7f7f7 60%,#ffffff 100%)}
.staff-cta{position:absolute;left:328px;top:2009px;width:182px;text-align:center}
.staff-member{position:absolute;width:250px}
.staff-member h4{font-size:15px;font-weight:700;text-transform:uppercase}
.staff-member .role{font-size:15px;margin-bottom:10px}
.staff-member p{font-size:12.5px;line-height:20px;color:#666}
.staff-member em{color:var(--ink)}

/* alerts & policies */
.notice-band{position:absolute;top:2126px;left:0;width:1200px;height:521px;background:var(--page)}
.panel{position:absolute;top:2188px;height:391px;background:var(--white);border:7px solid var(--blue-soft);padding:32px 32px}
.panel h3{font-size:21px;font-weight:600;text-transform:uppercase;display:flex;align-items:center;gap:10px;margin-bottom:26px}
.alert-item{display:flex;gap:18px;margin-bottom:28px}
.alert-item svg{flex-shrink:0;width:72px;height:76px}
.alert-item h5{font-size:12.5px;font-weight:700;text-transform:uppercase;line-height:19px;margin-bottom:8px}
.alert-item p{font-size:12.5px;line-height:20px;color:#666}
.policy-list{list-style:none;font-size:12.5px;font-weight:700;text-transform:uppercase}
.policy-list li{margin-bottom:10px;padding-left:14px;position:relative}
.policy-list li::before{content:"";position:absolute;left:0;top:7px;width:5px;height:5px;background:var(--ink);border-radius:50%}
.panel .btn{position:absolute;left:32px;bottom:30px}

/* location */
.map{position:absolute;top:2769px;left:0;width:1200px;height:443px;background:linear-gradient(135deg,#ece8df 0%,#e4e9dc 50%,#e9e4da 100%)}
.map-label{position:absolute;left:580px;top:2946px;width:192px;height:108px;background:var(--blue);color:var(--white);padding:14px 16px;font-size:12.5px;line-height:19px}
.map-label b{display:block;margin-bottom:4px}
.map-label::after{content:"";position:absolute;left:40px;bottom:-12px;border:12px solid transparent;border-bottom:0;border-top-color:var(--blue)}
.zoom{position:absolute;left:1155px;width:26px;height:26px;background:var(--white);border:1px solid #ccc;font-size:16px;text-align:center;line-height:24px;color:#555}

/* footer */
.site-footer{position:absolute;top:3212px;left:0;width:1200px;height:46px;background:var(--footer);color:#ccc;font-size:12px;display:flex;align-items:center;justify-content:space-between;padding:0 16px}
.site-footer a{color:#ccc}
</style>
</head>
<body>

<header class="site-header">
  <div class="brand">CLINIC NAME</div>
  <nav class="main-nav">
    <a class="active" href="#" style="left:483px">Home</a>
    <a href="#" style="left:567px">Our Clinic</a>
    <a href="#" style="left:690px">Our Staff</a>
    <a href="#" style="left:806px">Resources</a>
    <a href="#" style="left:926px">Alerts</a>
    <a href="#" style="left:1021px">Contact Us</a>
  </nav>
</header>

<section class="hero" role="img" aria-label="Photo of smiling physicians in a bright clinic hallway">
  <a class="hero-arrow" style="left:10px" href="#" aria-label="Previous slide">
    <svg width="14" height="14" viewBox="0 0 14 14"><path d="M9 2 4 7l5 5" fill="none" stroke="#fff" stroke-width="2.2"/></svg>
  </a>
  <a class="hero-arrow" style="left:1150px" href="#" aria-label="Next slide">
    <svg width="14" height="14" viewBox="0 0 14 14"><path d="M5 2l5 5-5 5" fill="none" stroke="#fff" stroke-width="2.2"/></svg>
  </a>
  <h1 class="hero-title"><strong>Free online lorem ipsum</strong>Generator with great features</h1>
</section>

<div class="info-band"></div>

<article class="card" style="left:76px">
  <h3><svg width="18" height="20" viewBox="0 0 18 20"><circle cx="9" cy="5" r="4.5" fill="var(--blue)"/><path d="M0 20c0-6 4-9 9-9s9 3 9 9z" fill="var(--blue)"/></svg>New Patients</h3>
  <p>Accepting new patients</p>
  <a class="btn" href="#">Contact Us</a>
</article>

<article class="card" style="left:434px">
  <h3><svg width="20" height="20" viewBox="0 0 20 20"><circle cx="10" cy="10" r="8.5" fill="none" stroke="var(--blue)" stroke-width="2.5"/><path d="M10 5v5l3.5 2" fill="none" stroke="var(--blue)" stroke-width="2.2"/></svg>Hours of Operation</h3>
  <ul class="rows">
    <li><b>Monday</b><span>8:00am - 6:00pm</span></li>
    <li><b>Tuesday</b><span>8:00am - 6:00pm</span></li>
    <li><b>Wednesday</b><span>8:00am - 6:00pm</span></li>
    <li><b>Thursday</b><span>8:00am - 6:00pm</span></li>
    <li><b>Friday</b><span>8:00am - 6:00pm</span></li>
    <li><b>Saturday</b><span>9:00am - 4:00pm</span></li>
    <li><b>Sunday</b><span>9:00am - 4:00pm</span></li>
  </ul>
</article>

<article class="card" style="left:793px;width:342px">
  <h3><svg width="20" height="16" viewBox="0 0 20 16"><rect x="0" y="0" width="20" height="16" rx="2" fill="var(--blue)"/><path d="M1 2l9 7 9-7" fill="none" stroke="#fff" stroke-width="1.8"/></svg>Contact Info</h3>
  <ul class="rows contact-rows">
    <li><b>Telephone</b><span>604 555 0182</span></li>
    <li><b>Fax</b><span>604 555 0183</span></li>
    <li><b>Email</b><a href="#">contact@clinicname.co</a></li>
    <li class="tall"><b>Address</b><span>123 Main Street,<br>Harbourview, B.C.<br>Canada, V2K4R7</span></li>
    <li><b>Directions</b><a href="#">Wayline Maps</a></li>
  </ul>
</article>

<section class="about">
  <h2><svg width="22" height="26" viewBox="0 0 22 26"><rect x="1" y="3" width="20" height="22" rx="2" fill="none" stroke="#fff" stroke-width="2.4"/><rect x="7" y="0" width="8" height="6" rx="1" fill="#fff"/><path d="M11 11v9M6.5 15.5h9" stroke="#fff" stroke-width="2.6"/></svg>About Our Clinic</h2>
  <p>Lorem Ipsum is simply dummy text of the printing and typesetting industry. Lorem Ipsum has been the industry's standard dummy text ever since the 1500s, when an unknown printer took a galley of type and scrambled it to make a type specimen book. It has survived not only five centuries, but also the leap into electronic typesetdesktop publishing software like Quillset Layout including versions of Lorem Ipsum.</p>
  <p>Lorem Ipsum is simply dummy text of the printing and typesetting industry. It has survived not only five centuries, but also the leap into electronic desktop publishing software like Quillset Layout including versions of Lorem Ipsum.</p>
</section>

<h2 class="section-title" style="top:1545px"><svg width="30" height="22" viewBox="0 0 30 22"><circle cx="15" cy="6" r="5" fill="#222"/><path d="M6 22c0-6 4-9 9-9s9 3 9 9z" fill="#222"/><circle cx="5.5" cy="8" r="3.5" fill="#222"/><circle cx="24.5" cy="8" r="3.5" fill="#222"/><path d="M0 20c0-4 2-7 6-7l1 1c-2 1-2.5 4-2.5 6zM30 20c0-4-2-7-6-7l-1 1c2 1 2.5 4 2.5 6z" fill="#222"/></svg>Our Staff</h2>

<div class="staff-photo" role="img" aria-label="Portrait photo of two clinic physicians"></div>
<a class="btn staff-cta" href="#">View All Staff</a>

<div class="staff-member" style="left:614px;top:1621px"><h4>Dr. John Smith, MD</h4><div class="role">Physician</div><p>In publishing and graphic design, lorem ipsum graphic elements of a document or visual presentation. <em>[Read more]</em></p></div>
<div class="staff-member" style="left:882px;top:1621px"><h4>Dr. John Smith, MD</h4><div class="role">Physician</div><p>In publishing and graphic design, lorem ipsum graphic elements of a document or visual presentation. <em>[Read more]</em></p></div>
<div class="staff-member" style="left:614px;top:1785px"><h4>Dr. John Smith, MD</h4><div class="role">Physician</div><p>In publishing and graphic design, lorem ipsum graphic elements of a document or visual presentation. <em>[Read more]</em></p></div>
<div class="staff-member" style="left:882px;top:1785px"><h4>Dr. John Smith, MD</h4><div class="role">Physician</div><p>In publishing and graphic design, lorem ipsum graphic elements of a document or visual presentation. <em>[Read more]</em></p></div>
<div class="staff-member" style="left:614px;top:1949px"><h4>Dr. John Smith, MD</h4><div class="role">Physician</div><p>In publishing and graphic design, lorem ipsum graphic elements of a document or visual presentation. <em>[Read more]</em></p></div>
<div class="staff-member" style="left:882px;top:1949px"><h4>Dr. John Smith, MD</h4><div class="role">Physician</div><p>In publishing and graphic design, lorem ipsum graphic elements of a document or visual presentation. <em>[Read more]</em></p></div>

<div class="notice-band"></div>

<section class="panel" style="left:76px;width:508px">
  <h3><svg width="18" height="20" viewBox="0 0 18 20"><path d="M9 1c-4 0-6 3-6 7v5l-2 3h16l-2-3V8c0-4-2-7-6-7z" fill="var(--blue)"/><circle cx="9" cy="18" r="2" fill="var(--blue)"/></svg>Alerts</h3>
  <div class="alert-item">
    <svg viewBox="0 0 44 46"><rect x="2" y="6" width="40" height="38" rx="3" fill="#fff" stroke="var(--blue)" stroke-width="2.5"/><rect x="2" y="6" width="40" height="9" fill="var(--blue)"/><rect x="10" y="1" width="4" height="9" rx="1" fill="var(--blue)"/><rect x="30" y="1" width="4" height="9" rx="1" fill="var(--blue)"/><text x="22" y="38" text-anchor="middle" font-family="Open Sans, sans-serif" font-size="19" font-weight="600" fill="var(--blue)">23</text></svg>
    <div><h5>A handy ipsum generator for all layout needs</h5><p>In publishing and graphic design, lorem as ipsum is filler text commonly used to demo nstrate the graphic elements of a aliquam erat volutpat. Ut wisi enim ...</p></div>
  </div>
  <div class="alert-item">
    <svg viewBox="0 0 44 46"><rect x="2" y="6" width="40" height="38" rx="3" fill="#fff" stroke="var(--blue)" stroke-width="2.5"/><rect x="2" y="6" width="40" height="9" fill="var(--blue)"/><rect x="10" y="1" width="4" height="9" rx="1" fill="var(--blue)"/><rect x="30" y="1" width="4" height="9" rx="1" fill="var(--blue)"/><text x="22" y="38" text-anchor="middle" font-family="Open Sans, sans-serif" font-size="19" font-weight="600" fill="var(--blue)">23</text></svg>
    <div><h5>A handy ipsum generator for all layout needs</h5><p>In publishing and graphic design, lorem as ipsum is filler text commonly used to demo nstrate the graphic elements of a aliquam erat volutpat. Ut wisi enim ...</p></div>
  </div>
</section>

<section class="panel" style="left:616px;width:508px">
  <h3><svg width="16" height="20" viewBox="0 0 16 20"><path d="M0 0h10l6 6v14H0z" fill="var(--blue)"/><path d="M10 0v6h6" fill="#8fd2ef"/></svg>Clinic Policies</h3>
  <ul class="policy-list">
    <li>Late arrivals</li>
    <li>Missed appointments</li>
    <li>Fees</li>
  </ul>
  <a class="btn" href="#">View All Clinic Policies</a>
</section>

<h2 class="section-title" style="top:2690px"><svg width="16" height="22" viewBox="0 0 16 22"><path d="M8 0C3.6 0 0 3.4 0 7.8 0 13 8 22 8 22s8-9 8-14.2C16 3.4 12.4 0 8 0z" fill="#222"/><circle cx="8" cy="8" r="3" fill="#fff"/></svg>Our Location</h2>

<div class="map" role="img" aria-label="Street map around the clinic location"></div>
<div class="map-label"><b>Clinic Name</b>226, Lorem ipsum dolor sit, dolor Intelle - 258458</div>
<div class="zoom" style="top:3152px">+</div>
<div class="zoom" style="top:3178px">−</div>

<footer class="site-footer">
  <span>©2015 Clinic Name. All Rights Reserved</span>
  <span><a href="#">Terms &amp; Privacy Policy</a> | <a href="#">Sitemap</a></span>
</footer>

</body>
</html>
```